Business Card Design - Amberfield Court

We are looking at a new design for our business cards that has a modern and professional look. We run a residential aged care facility focussing on the care of residents. The cards will be used for potential clients, consultants and business opportunities in this sector. Blue and white is our main colours and would to see these colours incorporated in the design.
Industry/Entity Type
Business
Contact Information for Business Card
Amberfield Court, Darren Walsh, dwalsh@amberfieldcourt.com.au, Finance Manager, 0472 639 208, BCom, 37 Marrabel Crescent, Brindle Vale, Qld 4093.
Look and feel
Each slider illustrates characteristics of the customer's brand and the style your logo design should communicate.

```html
<!DOCTYPE html>
<html lang="en">
<head>
<meta charset="UTF-8">
<title>Amberfield Court – Business Card</title>
<link href="https://fonts.googleapis.com/css2?family=Source+Sans+3:wght@400;600&display=swap" rel="stylesheet">
<style>
  :root {
    --backdrop: #2f2f31;
    --card: #141416;
    --brand-blue: #4f7f9e;
    --text-light: #e6e8ea;
    --divider: #2a2a2d;
    --band: #c3b6aa;
    --band-text: #1b1b1d;
  }
  * { margin: 0; padding: 0; box-sizing: border-box; }
  html, body { width: 1200px; height: 900px; overflow: hidden; }
  body {
    background: var(--backdrop);
    font-family: "Source Sans 3", sans-serif;
    position: relative;
  }
  .card {
    position: absolute;
    top: 300px;
    width: 500px;
    height: 300px;
    border-radius: 22px;
    background: var(--card);
    box-shadow: 0 10px 30px rgba(0,0,0,.45);
    overflow: hidden;
  }
  .card--front { left: 70px; }
  .card--back { left: 630px; }

  /* front */
  .front-brand {
    position: absolute;
    left: 30px;
    top: 128px;
    display: flex;
    align-items: center;
    gap: 12px;
  }
  .brand-dot {
    width: 26px; height: 26px;
    border-radius: 50%;
    background: var(--brand-blue);
    flex: none;
  }
  .brand-name {
    color: var(--brand-blue);
    font-weight: 600;
    font-size: 20px;
    letter-spacing: .02em;
    white-space: nowrap;
  }
  .front-divider {
    position: absolute;
    left: 252px; top: 40px;
    width: 1px; height: 220px;
    background: var(--divider);
  }
  .contact {
    position: absolute;
    left: 272px;
    right: 20px;
    top: 52px;
    color: var(--text-light);
    font-size: 13.5px;
    line-height: 1.4;
  }
  .contact__name {
    color: var(--brand-blue);
    font-weight: 600;
    font-size: 21px;
    line-height: 1.1;
    white-space: nowrap;
  }
  .contact__degree { font-size: 12px; font-weight: 400; }
  .contact__role { margin-bottom: 22px; }
  .contact__address { margin-bottom: 22px; }
  .contact__line { display: flex; align-items: center; gap: 7px; white-space: nowrap; }
  .contact__line svg { width: 11px; height: 11px; fill: var(--brand-blue); flex: none; }

  /* back */
  .back-brand {
    position: absolute;
    left: 0; right: 0; top: 108px;
    display: flex;
    flex-direction: column;
    align-items: center;
    gap: 14px;
  }
  .back-brand .brand-row { display: flex; align-items: center; gap: 12px; }
  .back-brand .brand-dot { width: 30px; height: 30px; }
  .back-brand .brand-name { font-size: 26px; }
  .tagline {
    background: var(--band);
    color: var(--band-text);
    font-size: 14px;
    padding: 3px 14px;
    white-space: nowrap;
  }
</style>
</head>
<body>
  <section class="card card--front" aria-label="Business card front">
    <div class="front-brand">
      <span class="brand-dot"></span>
      <span class="brand-name">Amberfield Court</span>
    </div>
    <div class="front-divider"></div>
    <div class="contact">
      <p class="contact__name">Darren Walsh<span class="contact__degree">, BCom</span></p>
      <p class="contact__role">Finance Manager</p>
      <p class="contact__address">37 Marrabel Crescent,<br>Brindle Vale, Qld 4093</p>
      <p class="contact__line">
        <svg viewBox="0 0 24 24" aria-hidden="true"><path d="M6.6 10.8a15.1 15.1 0 0 0 6.6 6.6l2.2-2.2a1 1 0 0 1 1-.25 11.4 11.4 0 0 0 3.6.57 1 1 0 0 1 1 1V20a1 1 0 0 1-1 1A17 17 0 0 1 3 4a1 1 0 0 1 1-1h3.5a1 1 0 0 1 1 1c0 1.25.2 2.45.57 3.57a1 1 0 0 1-.25 1z"/></svg>
        0472 639 208
      </p>
      <p class="contact__line">
        <svg viewBox="0 0 24 24" aria-hidden="true"><path d="M2 5h20v14H2z M2 5l10 8 10-8" /></svg>
        dwalsh@amberfieldcourt.com.au
      </p>
    </div>
  </section>

  <section class="card card--back" aria-label="Business card back">
    <div class="back-brand">
      <div class="brand-row">
        <span class="brand-dot"></span>
        <span class="brand-name">Amberfield Court</span>
      </div>
      <p class="tagline">Comfort, Respect, Belonging</p>
    </div>
  </section>
</body>
</html>
```